Corvane Paintless Dent Removal

Our company works on vehicles removing dents using a highly skilled trade which the metal is massaged out with special tools without disturbing the original paint, hence paintless dent removal. Besides keeping the paint and metal original its also very environmentally friendly since no paint or toxic fillers are used. Also we we are one of the most experienced companies in the business with 25 years

Target Market(s)

Retail Automobile consumers, Auto Dealerships and Auto Body Shops

Industry/Entity Type

Auto Repair

Contact Information for Business Card

Dale Hollister
PO Box 518 Brookmere, NY 11962
631-555-0148
corvanepdr@mailbox-example.com
website corvanepdr.example
youtube corvane paintless dent removal
25 years of experience removing Dents, Dings and Hail Damage

Font styles to use
Serif
Sans Serif

Colors

Designer to choose colors to be used in the design.

Requirements
Must have
• I do like things that are simple but classy and somewhat bold, also I like my logo so that should be somewhat important

```html
<!DOCTYPE html>
<html lang="en">
<head>
<meta charset="utf-8">
<title>Corvane Paintless Dent Removal – Business Card</title>
<link href="https://fonts.googleapis.com/css2?family=Roboto:wght@400;500;700;900&display=swap" rel="stylesheet">
<style>
  :root {
    --backdrop: #3a3a3a;
    --card-black: #1e1e20;
    --card-charcoal: #262628;
    --emboss: #3b3b3e;
    --lime: #8cc63f;
    --navy: #152a57;
    --navy-deep: #0f2149;
    --steel: #3d3d40;
    --white: #ffffff;
    --muted: #d8d8d8;
    --accent-red: #e02b2b;
  }
  * { margin: 0; padding: 0; box-sizing: border-box; }
  html, body { width: 799px; height: 1200px; overflow: hidden; }
  body {
    background: var(--backdrop);
    font-family: "Roboto", Arial, sans-serif;
    position: relative;
  }
  .card {
    position: absolute;
    left: 50px;
    width: 700px;
    height: 400px;
    border-radius: 4px;
    overflow: hidden;
    box-shadow: 0 14px 30px rgba(0,0,0,.45);
  }
  .card--front { top: 120px; background: var(--card-black); }
  .card--back  { top: 680px; background: var(--card-charcoal); }

  /* front: brand name set as tone-on-tone text */
  .front-brand {
    position: absolute; inset: 0;
    display: flex; flex-direction: column; align-items: center; justify-content: center;
    color: var(--emboss);
    font-weight: 900;
    text-transform: uppercase;
    text-align: center;
  }
  .front-brand__name { font-size: 74px; letter-spacing: 2px; line-height: 1; }
  .front-brand__trade { font-size: 30px; letter-spacing: 1px; margin-top: 10px; }

  /* back */
  .back-waves { position: absolute; inset: 0; width: 100%; height: 100%; }
  .person { position: absolute; left: 42px; top: 40px; }
  .person__name { color: var(--lime); font-size: 32px; font-weight: 700; }
  .person__role { color: var(--muted); font-size: 15px; margin-top: 2px; }

  .contacts { position: absolute; left: 42px; top: 126px; list-style: none; }
  .contacts li {
    display: flex; align-items: center; gap: 12px;
    color: var(--white); font-size: 17px; height: 25px;
  }
  .contacts li.address { margin-left: 0; }
  .contacts svg { width: 16px; height: 16px; flex: none; }
  .contacts .spacer { width: 16px; flex: none; }

  .back-brand {
    position: absolute; right: 40px; top: 135px;
    display: flex; align-items: center; gap: 12px;
  }
  .back-brand__dot { width: 22px; height: 22px; border-radius: 50%; background: var(--lime); }
  .back-brand__text {
    color: var(--lime); font-weight: 700; font-size: 22px; line-height: 1.15;
  }
  .back-brand__text span { display: block; }
  .back-brand__text .big { font-size: 40px; text-transform: uppercase; letter-spacing: 1px; }

  .tagline {
    position: absolute; right: 40px; bottom: 32px;
    color: var(--white); font-size: 19px; line-height: 1.3; text-align: right;
  }
</style>
</head>
<body>

<section class="card card--front" aria-label="Card front">
  <div class="front-brand">
    <span class="front-brand__name">Corvane</span>
    <span class="front-brand__trade">Paintless Dent Removal</span>
  </div>
</section>

<section class="card card--back" aria-label="Card back">
  <svg class="back-waves" viewBox="0 0 700 400" preserveAspectRatio="none" aria-hidden="true">
    <path d="M0 262 C120 250 200 300 330 300 C460 300 560 282 700 300 L700 400 L0 400 Z" fill="var(--steel)"/>
    <path d="M0 240 C60 232 150 300 300 306 C450 312 580 285 700 292 L700 306 C580 300 450 325 300 320 C150 314 60 250 0 256 Z" fill="var(--lime)"/>
    <path d="M0 282 C120 282 190 330 330 330 C470 330 580 305 700 312 L700 400 L0 400 Z" fill="var(--navy)"/>
  </svg>

  <div class="person">
    <h1 class="person__name">Dale Hollister</h1>
    <p class="person__role">Managing Director</p>
  </div>

  <ul class="contacts">
    <li class="address"><span class="spacer"></span>PO Box 518 Brookmere, NY 11962</li>
    <li>
      <svg viewBox="0 0 16 16"><path d="M3 1h3l1.5 4-2 1.3a9 9 0 0 0 4.2 4.2L11 8.5l4 1.5v3a2 2 0 0 1-2 2A12 12 0 0 1 1 3a2 2 0 0 1 2-2z" fill="var(--lime)"/></svg>
      631-555-0148
    </li>
    <li>
      <svg viewBox="0 0 16 16"><rect x="1" y="3" width="14" height="10" fill="var(--lime)"/><path d="M1 3l7 6 7-6" stroke="var(--card-charcoal)" stroke-width="1.4" fill="none"/></svg>
      corvanepdr@mailbox-example.com
    </li>
    <li>
      <svg viewBox="0 0 16 16"><circle cx="8" cy="8" r="6.5" fill="none" stroke="var(--lime)" stroke-width="1.6"/><path d="M1.5 8h13M8 1.5c-3 3.5-3 9.5 0 13M8 1.5c3 3.5 3 9.5 0 13" stroke="var(--lime)" stroke-width="1.3" fill="none"/></svg>
      www.corvanepdr.example
    </li>
    <li>
      <svg viewBox="0 0 16 16"><rect x="1" y="3" width="14" height="10" rx="2" fill="var(--accent-red)"/></svg>
      /Dale Hollister
    </li>
  </ul>

  <div class="back-brand">
    <span class="back-brand__dot"></span>
    <p class="back-brand__text"><span class="big">Corvane</span><span>Paintless Dent Removal</span></p>
  </div>

  <p class="tagline">25 years of<br>experience removing<br>Dents, Dings and Hail Damage</p>
</section>

</body>
</html>
```